Maple Lane HEMP Facial Oil and Body Oil Packaging Project

We need a packaging concept for a Hemp based facial oil and body oil. We need label design for the bottle and carton graphics. I am attaching a few reference photos. The target demographic is women between 17-35 year old. Products need to be able to stand out in crowded stores with clear calls to action.
1oz Dropper Bottle with Unit Carton - Hemp Facial Oil
4oz PET Bottle with Unit Carton - Hemp + Rose Facial Oil

```html
<!DOCTYPE html>
<html lang="en">
<head>
<meta charset="utf-8">
<title>Maple Lane Hemp Facial Oil – Packaging</title>
<link href="https://fonts.googleapis.com/css2?family=Oswald:wght@300;400&family=Open+Sans:wght@400;600&display=swap" rel="stylesheet">
<style>
  :root{
    --bg:#e9e9e9;
    --white:#ffffff;
    --leaf-pale:#e3ecd9;
    --leaf-mid:#c9d8b8;
    --ink-green:#1f4a1d;
    --olive-light:#8ea764;
    --olive-dark:#5d6f3f;
    --olive-ink:#3f4b2c;
  }
  *{margin:0;padding:0;box-sizing:border-box}
  html,body{width:1200px;height:1200px;overflow:hidden}
  body{background:var(--bg);position:relative;font-family:"Open Sans",sans-serif}

  .panel{position:absolute;background:var(--white);overflow:hidden;box-shadow:0 6px 18px rgba(0,0,0,.12)}
  .panel-top{position:absolute;left:0;top:0;width:100%}
  .leaf-pattern{position:absolute;inset:0;background:radial-gradient(circle at 30% 30%,var(--leaf-mid) 0,transparent 28%),radial-gradient(circle at 75% 65%,var(--leaf-mid) 0,transparent 30%),linear-gradient(160deg,var(--white),var(--leaf-pale))}
  .panel-bottom{position:absolute;left:0;bottom:0;width:100%;background:linear-gradient(180deg,var(--olive-light),var(--olive-dark));color:var(--white);text-align:center}

  .brand{position:relative;font-family:"Oswald",sans-serif;font-weight:300;color:var(--ink-green);text-align:center;letter-spacing:.5px}
  .headline{position:relative;font-family:"Oswald",sans-serif;font-weight:400;color:var(--ink-green);text-align:center;line-height:1}
  .sub-headline{position:relative;font-family:"Oswald",sans-serif;font-weight:300;color:var(--ink-green);text-align:center;line-height:1}

  /* side panel */
  .side{left:70px;top:120px;width:250px;height:960px}
  .side .panel-top{height:420px}
  .side .brand{font-size:28px;padding-top:150px}
  .side .headline{font-size:104px;margin-top:10px}
  .side .sub-headline{font-size:50px;margin-top:8px}
  .side .panel-bottom{height:540px;padding:36px 20px 0}
  .side .copy{font-family:"Oswald",sans-serif;font-weight:300;font-size:13px;line-height:24px;margin-bottom:22px}
  .side .volume{position:absolute;left:0;right:0;bottom:34px;font-family:"Oswald",sans-serif;font-weight:300;font-size:26px}

  /* front panel */
  .front{left:320px;top:120px;width:340px;height:960px}
  .front .panel-top{height:420px}
  .front .brand{font-size:36px;padding-top:150px}
  .front .headline{font-size:140px;margin-top:8px}
  .front .panel-bottom{height:540px;padding-top:30px}
  .drop{display:block;margin:0 auto}
  .front .product-name{font-size:58px;font-weight:400;line-height:1;margin-top:24px}
  .pill{display:inline-block;background:var(--white);color:var(--olive-ink);border-radius:26px;font-size:30px;letter-spacing:3px;padding:2px 36px;margin-top:14px}
  .bottle-icon{display:block;margin:28px auto 0}
  .front .volume{font-family:"Oswald",sans-serif;font-weight:300;font-size:28px;color:var(--olive-ink);margin-top:12px}

  /* bottle label */
  .label{left:720px;top:430px;width:410px;height:440px}
  .label .panel-top{height:110px}
  .label .brand{font-family:"Open Sans",sans-serif;font-size:14px;padding-top:20px}
  .label .headline{font-family:"Open Sans",sans-serif;font-size:52px;margin-top:0}
  .label .panel-bottom{height:330px;text-align:left}
  .label .product-name{position:absolute;left:36px;top:22px;font-size:50px;line-height:1.15}
  .label .pill{position:absolute;left:30px;top:148px;font-size:18px;letter-spacing:1px;padding:0 16px;border-radius:14px;margin-top:0}
  .label .drop{position:absolute;right:50px;top:60px;margin:0}
  .leaf-mark{position:absolute;left:40px;top:198px;width:66px;height:50px;border-radius:4px;background:var(--olive-dark)}
  .label .volume{position:absolute;left:44px;top:270px;font-size:22px}
</style>
</head>
<body>

  <section class="panel side" aria-label="Carton side panel">
    <div class="panel-top">
      <div class="leaf-pattern" role="img" aria-label="Soft green hemp leaf pattern"></div>
      <p class="brand">MAPLE LANE</p>
      <h2 class="headline">HEMP</h2>
      <p class="sub-headline">FACIAL OIL</p>
    </div>
    <div class="panel-bottom">
      <p class="copy">Lorem Ipsum is simply dummy text of the printing and typesetting industry. Lorem Ipsum has been the industry's standard dummy text ever since the 1500s, when an unknown printer took a galley of type and scrambled it to make a type specimen book.</p>
      <p class="copy">Lorem Ipsum is simply dummy text of the printing and typesetting industry. Lorem Ipsum has been the industry's standard dummy text ever since the 1500s, when an unknown printer took a galley of type and scrambled it to make a type specimen book.</p>
      <p class="volume">1 oz 30 ml</p>
    </div>
  </section>

  <section class="panel front" aria-label="Carton front panel">
    <div class="panel-top">
      <div class="leaf-pattern" role="img" aria-label="Soft green hemp leaf pattern"></div>
      <p class="brand">MAPLE LANE</p>
      <h1 class="headline">HEMP</h1>
    </div>
    <div class="panel-bottom">
      <svg class="drop" width="72" height="136" viewBox="0 0 90 170" aria-hidden="true">
        <circle cx="45" cy="6" r="5" fill="#fff"/>
        <path d="M45 22 C45 22 86 90 86 126 A41 41 0 0 1 4 126 C4 90 45 22 45 22Z" fill="#fff"/>
      </svg>
      <p class="product-name">FACIAL OIL</p>
      <span class="pill">WITH HEMP</span>
      <svg class="bottle-icon" width="32" height="74" viewBox="0 0 40 92" aria-hidden="true">
        <g fill="none" stroke="#56663a" stroke-width="3">
          <rect x="14" y="2" width="12" height="18" rx="6"/>
          <rect x="11" y="20" width="18" height="12"/>
          <rect x="3" y="32" width="34" height="58" rx="6"/>
          <line x1="20" y1="36" x2="20" y2="80"/>
        </g>
      </svg>
      <p class="volume">1 oz 30 ml</p>
    </div>
  </section>

  <section class="panel label" aria-label="Dropper bottle label">
    <div class="panel-top">
      <div class="leaf-pattern" role="img" aria-label="Soft green hemp leaf pattern"></div>
      <p class="brand">MAPLE LANE</p>
      <h2 class="headline">HEMP</h2>
    </div>
    <div class="panel-bottom">
      <p class="product-name">FACIAL<br>OIL</p>
      <span class="pill">WITH HEMP</span>
      <svg class="drop" width="110" height="160" viewBox="0 0 110 160" aria-hidden="true">
        <path d="M55 0 C55 0 106 70 106 106 A51 51 0 0 1 4 106 C4 70 55 0 55 0Z" fill="#fff"/>
      </svg>
      <div class="leaf-mark" role="img" aria-label="Small hemp leaf emblem"></div>
      <p class="volume">1 oz 30 ml</p>
    </div>
  </section>

</body>
</html>
```